CD Cover für junge Pop-Rock Band
Sehr kreative vorschläge. mehrere designs, die alle unter den top-favoriten für uns waren. änderungen und anpassungen stets schnell umgesetzt und auch nach gewinner-auswahl noch weiter zusammen gearbeitet bevor das endgültige design übergeben wurde.
Zielgruppe
Wir sind eine junge Band aus München und machen ausschließlich eigene Songs im Bereich Pop-Rock. Durch Einflüsse aus verschiedenen anderen Genres wie Funk, Reggae und Britpop grenzen sich unsere Songs von typischem Mainstream-Pop ab. Unsere Zielgruppe setzt sich aus Personen verschiedener Altersgruppen zusammen, der Fokus liegt jedoch auf Mitte Zwanzig- bis Mitte Dreißig-Jährigen.
Homepage: www.okapimind.com
Sozialnetz: www.sozialnetz.example/okapimindband
Aufgabenstellung
Wir benötigen ein Design für unsere neue EP "Open Gates". Diese wird in Form eines DigiPacks veröffentlicht werden. Daher werden Designs für Vorderseite, Rückseite, zwei Innenseiten sowie die CD selbst benötigt.
Folgendes sollte auf den jeweiligen Seiten enthalten sein:
Vorderseite:
- Bandschriftzug (siehe Anhang)
- Name der EP: Open Gates
Rückseite:
- Trackliste (1.Velvet Spoon, 2.Hold It Near, 3.Harbor Pike, 4.Can We Stay, 5.Brightest Edge)
- Credits (Recording by ..., Mix by ..., Mastering by ..., etc. -> wird noch festgesetzt)
Anmerkung:
Die roten Kratzer aus dem Bandlogo können bei Bedarf frei verwendet werden hinsichtlich Farbe, Muster, Gestaltung, Größe, etc.
Wir möchten keine Bilder von uns (z.B. von unserer Homepage, Sozialnetz, etc) auf der CD.

```html
<!DOCTYPE html>
<html lang="en">
<head>
<meta charset="utf-8">
<title>Okapimind – Open Gates – Disc Label</title>
<link rel="stylesheet" href="https://fonts.googleapis.com/css2?family=Source+Sans+3:wght@300;400&display=swap">
<style>
  :root {
    --page: #ffffff;
    --ink-light: #ffffff;
    --tone-light: #d9d9d9;
    --tone-mid: #8a8a8a;
    --tone-dark: #2a2a2a;
    --tone-deep: #111111;
    --rim: #cfcfcf;
  }
  html, body {
    margin: 0;
    padding: 0;
    width: 1200px;
    height: 1200px;
    overflow: hidden;
    background: var(--page);
  }
  .disc-label {
    position: relative;
    width: 1200px;
    height: 1200px;
    font-family: "Source Sans 3", "Helvetica Neue", Arial, sans-serif;
    color: var(--ink-light);
  }
  .disc-art {
    position: absolute;
    inset: 0;
  }
  .band-name {
    position: absolute;
    top: 190px;
    left: 0;
    width: 1200px;
    text-align: center;
    font-weight: 300;
    font-size: 92px;
    letter-spacing: 2px;
    line-height: 1;
    margin: 0;
  }
  .ep-title {
    position: absolute;
    top: 568px;
    font-weight: 400;
    font-size: 76px;
    letter-spacing: 2px;
    line-height: 1;
    margin: 0;
  }
  .ep-title--left { left: 92px; }
  .ep-title--right { right: 128px; }
  .track-list {
    position: absolute;
    top: 808px;
    left: 465px;
    margin: 0;
    padding: 0;
    list-style: none;
    font-weight: 400;
    font-size: 37px;
    line-height: 65.5px;
  }
</style>
</head>
<body>
<main class="disc-label">
  <svg class="disc-art" width="1200" height="1200" viewBox="0 0 1200 1200">
    <defs>
      <radialGradient id="photo-tones" cx="42%" cy="45%" r="62%">
        <stop offset="0%" stop-color="var(--tone-mid)"/>
        <stop offset="45%" stop-color="var(--tone-dark)"/>
        <stop offset="75%" stop-color="#5a5a5a"/>
        <stop offset="100%" stop-color="var(--tone-deep)"/>
      </radialGradient>
      <mask id="disc-hole">
        <rect width="1200" height="1200" fill="#fff"/>
        <circle cx="600" cy="600" r="70" fill="#000"/>
      </mask>
    </defs>
    <g mask="url(#disc-hole)">
      <circle class="disc-photo" cx="600" cy="600" r="597" fill="url(#photo-tones)"
              role="img" aria-label="Black and white photograph of two zebras with bold striped coats filling the disc"/>
    </g>
    <circle class="disc-rim" cx="600" cy="600" r="597" fill="none" stroke="var(--rim)" stroke-width="2"/>
    <circle class="disc-hole-edge" cx="600" cy="600" r="70" fill="var(--page)" stroke="var(--rim)" stroke-width="1"/>
  </svg>

  <h1 class="band-name">OKAPIMIND</h1>

  <h2 class="ep-title ep-title--left">OPEN</h2>
  <h2 class="ep-title ep-title--right">GATES</h2>

  <ol class="track-list">
    <li>1. Velvet Spoon</li>
    <li>2. Hold It Near</li>
    <li>3. Harbor Pike</li>
    <li>4. Can We Stay</li>
    <li>5. Brightest Edge</li>
  </ol>
</main>
</body>
</html>
```